Natural Supplement Co Needs Label Makeover

Our company's success began with our main product, an amino acid blend that aids in fat metabolism, called Vantorel. Since then we continue to expand the product line that now includes a detox called Vantopurge, and probiotic called Vantoflora, as well as 3 others, for a total of 6 products/ labels.
Our original design/logo had more of an 'old-timey' feel (see attached 2-product photo). We are looking for a fresh label design update for the product line which reflects the range of supplements as cohesive and individual parts of an overall health plan/strategy (see attached 'Logo Update Test' as just one idea we had in-house, you need not consider it as a starting point).

Target Market(s)

women 25-45

Industry/Entity Type

Health And Wellness

Requirements
Must have
• consistent theme with confident look
Nice to have
• Each product (ie. "Vantorel") has a few-word descriptor: ("Fat-Burning Amino Acids") that should be planned on including as part of each label.
Should not have
• NO 'streamlined' or graphic interpretations of the human body, or figurative image

```html
<!DOCTYPE html>
<html lang="en">
<head>
<meta charset="utf-8">
<title>Vantopurge Label</title>
<link href="https://fonts.googleapis.com/css2?family=Fira+Sans+Condensed:wght@500;600;700&display=swap" rel="stylesheet">
<style>
  :root {
    --page-bg: #ececec;
    --label-white: #ffffff;
    --brand-blue: #1a6bb8;
    --brand-blue-light: #3f93d8;
    --brand-blue-deep: #1459a0;
    --swoosh-black: #1d1d1f;
    --text-white: #ffffff;
  }
  * { margin: 0; padding: 0; box-sizing: border-box; }
  html, body {
    width: 960px;
    height: 1200px;
    overflow: hidden;
    background: var(--page-bg);
    font-family: "Fira Sans Condensed", "Arial Narrow", sans-serif;
  }
  .label {
    position: absolute;
    left: 110px;
    top: 50px;
    width: 740px;
    height: 1100px;
    background: var(--label-white);
  }
  .label-shapes {
    position: absolute;
    inset: 0;
    width: 740px;
    height: 1100px;
  }
  .descriptor {
    position: absolute;
    left: 100px;
    width: 560px;
    top: 92px;
    text-align: center;
    color: var(--text-white);
    font-weight: 600;
    font-size: 84px;
    line-height: 1;
  }
  .product-name {
    position: absolute;
    left: 0;
    width: 740px;
    top: 385px;
    text-align: center;
    color: var(--brand-blue);
    font-weight: 600;
    font-size: 138px;
    line-height: 1;
    letter-spacing: -1px;
  }
  .category {
    position: absolute;
    left: 60px;
    width: 660px;
    top: 770px;
    text-align: center;
    color: var(--text-white);
    font-weight: 600;
    font-size: 90px;
    line-height: 1;
  }
  .tagline {
    position: absolute;
    left: 60px;
    width: 660px;
    top: 905px;
    text-align: center;
    color: var(--text-white);
    font-weight: 500;
    font-size: 52px;
    line-height: 1;
  }
  .volume {
    position: absolute;
    left: 60px;
    width: 660px;
    top: 1040px;
    text-align: center;
    color: var(--text-white);
    font-weight: 500;
    font-size: 28px;
    line-height: 1;
  }
</style>
</head>
<body>
  <main class="label">
    <svg class="label-shapes" viewBox="0 0 740 1100" aria-hidden="true">
      <defs>
        <linearGradient id="blue-band" x1="0" y1="0" x2="1" y2="0">
          <stop offset="0" stop-color="var(--brand-blue-deep)"/>
          <stop offset="0.6" stop-color="var(--brand-blue)"/>
          <stop offset="1" stop-color="var(--brand-blue-light)"/>
        </linearGradient>
      </defs>
      <path class="top-band" fill="url(#blue-band)"
            d="M100 0 H740 V165 C600 212 420 292 262 286 C152 282 100 240 100 180 Z"/>
      <path class="top-swoosh" fill="var(--swoosh-black)"
            d="M190 287 C380 302 560 232 740 168 V196 C560 258 380 314 190 287 Z"/>
      <path class="bottom-swoosh" fill="var(--swoosh-black)"
            d="M0 682 C200 624 520 618 740 702 V742 C520 662 200 668 0 722 Z"/>
      <path class="bottom-band" fill="url(#blue-band)"
            d="M0 722 C200 668 520 662 740 742 V1100 H0 Z"/>
    </svg>
    <p class="descriptor">Fat Burning</p>
    <h1 class="product-name">Vantopurge</h1>
    <p class="category">AMINO ACIDS</p>
    <p class="tagline">All Natural Supplement</p>
    <p class="volume">1 FL. OZ (30 ml)</p>
  </main>
</body>
</html>
```